bail bonds business

Need a web design for a Bail Bond company. At Fernlow Bails, we specialize in getting arrested defendants out of jail. Also, I have all the necessary information already uploaded in the files.

Target Market(s)

Arrested defendants and their families who will post bails on their behalf.

Industry/Entity Type

Business

Coding

Coded - Design and coding required

Number of Pages Required

1 page

```html
<!DOCTYPE html>
<html lang="en">
<head>
<meta charset="utf-8">
<title>Fernlow Bails</title>
<link rel="stylesheet" href="https://fonts.googleapis.com/css2?family=Open+Sans:wght@300;400;600;700&display=swap">
<style>
:root{
  --red:#d8232a;
  --blue:#2f6fb3;
  --ink:#333333;
  --muted:#8a8a8a;
  --dark:#2b2b2b;
  --darker:#1e1e1e;
  --grey-bg:#eeeeee;
  --white:#ffffff;
}
*{box-sizing:border-box;margin:0;padding:0}
html,body{width:1200px;height:2516px;overflow:hidden}
body{font-family:"Open Sans",Arial,sans-serif;color:var(--ink);background:var(--white);position:relative}
.topbar{position:absolute;top:0;left:0;width:1200px;height:28px;background:var(--white);font-size:11px;color:#555;display:flex;justify-content:flex-end;gap:40px;padding:8px 40px 0}
.brand{position:absolute;top:40px;left:0;width:1200px;text-align:center}
.brand-row{display:inline-flex;align-items:center;gap:12px}
.brand-dot{width:44px;height:44px;border-radius:50%;background:var(--red)}
.brand-name{font-size:30px;font-weight:700;color:var(--dark);letter-spacing:1px;text-transform:uppercase}
.hero{position:absolute;top:176px;left:0;width:1200px;height:564px;background:linear-gradient(180deg,#4a4642 0%,#7d756d 45%,#5b544e 100%)}
.nav{position:absolute;top:0;left:0;width:1200px;height:34px;background:rgba(20,20,20,.55);display:flex;justify-content:center;gap:56px;align-items:center}
.nav a{font-size:12px;font-weight:600;color:var(--white);text-decoration:none;text-transform:uppercase}
.nav a.active{color:var(--red)}
.hero-title{position:absolute;top:250px;width:1200px;text-align:center;color:var(--white);font-size:50px;font-weight:700;letter-spacing:1px}
.dots{position:absolute;top:506px;width:1200px;display:flex;justify-content:center;gap:8px}
.dots span{width:9px;height:9px;border-radius:50%;background:rgba(255,255,255,.6)}
.dots span.on{background:var(--white)}
.section-title{font-size:42px;font-weight:300;text-transform:uppercase;text-align:center;color:var(--dark)}
.section-sub{font-size:13px;color:#666;text-align:center;margin-top:10px}
.about{position:absolute;top:775px;left:0;width:1200px}
.about-list{position:absolute;top:122px;left:180px;width:860px}
.about-item{display:flex;gap:36px;height:112px}
.about-icon{width:60px;height:60px;flex:none}
.about-item h3{font-size:16px;font-weight:600;color:var(--dark);margin-bottom:10px}
.about-item p{font-size:12px;line-height:1.6;color:var(--muted)}
.offer{position:absolute;top:1248px;left:0;width:1200px;height:520px;background:var(--grey-bg);padding-top:30px}
.offer-grid{position:absolute;top:130px;left:40px;width:1140px;display:grid;grid-template-columns:1fr 1fr;column-gap:60px;row-gap:34px}
.offer-item h4{display:flex;align-items:center;gap:12px;font-size:13px;font-weight:700;color:var(--dark);text-transform:uppercase;margin-bottom:10px}
.offer-item p{font-size:11px;line-height:1.6;color:var(--muted);padding-left:36px;width:460px}
.service{position:absolute;top:1780px;left:0;width:1200px;height:440px;background:linear-gradient(160deg,#3b2a20 0%,#6a4c35 45%,#a88a66 75%,#4a3526 100%)}
.service-box{position:absolute;top:168px;left:380px;width:708px;height:124px;background:rgba(255,255,255,.93);text-align:center;padding-top:30px}
.service-box h2{font-size:36px;font-weight:300;text-transform:uppercase;color:var(--dark)}
.service-box p{font-size:12px;color:#666;margin-top:6px}
.newsletter{position:absolute;top:2278px;left:0;width:1200px;text-align:center}
.newsletter h2{font-size:36px;font-weight:300;text-transform:uppercase;color:var(--dark)}
.signup{margin:32px auto 0;width:340px;height:34px;display:flex;border:1px solid #cfcfcf}
.signup span{flex:1;font-size:11px;color:#aaa;text-align:left;padding:9px 12px}
.signup b{width:36px;background:var(--white);display:flex;align-items:center;justify-content:center}
.footer{position:absolute;top:2472px;left:0;width:1200px;height:44px;background:var(--darker);color:#ccc;font-size:11px;display:flex;align-items:center;justify-content:space-between;padding:0 40px}
.social{display:flex;gap:10px}
.social span{width:12px;height:12px;border-radius:50%;background:#cfcfcf}
</style>
</head>
<body>
<div class="topbar"><span>Call Us: (555) 014-2290</span><span>795 Harrow Blvd, Cedar Falls, NY 10482</span></div>
<header class="brand"><div class="brand-row"><span class="brand-dot"></span><span class="brand-name">Fernlow Bails Inc.</span></div></header>

<section class="hero" role="img" aria-label="Photo of hands reaching through jail bars toward a family member">
  <nav class="nav"><a class="active">Home</a><a>About Us</a><a>What We Offer</a><a>Our Services</a><a>Contact Us</a></nav>
  <h1 class="hero-title">WE BRING FAMILIES TOGETHER</h1>
  <div class="dots"><span></span><span class="on"></span><span></span></div>
</section>

<section class="about">
  <h2 class="section-title">About Us</h2>
  <p class="section-sub">At Fernlow Bails, getting your loved one out of jail fast is our first priority</p>
  <div class="about-list">
    <div class="about-item">
      <svg class="about-icon" viewBox="0 0 60 60"><path d="M8 30 L40 12 L30 30 L40 48 Z" fill="var(--red)"/><path d="M30 30 H54" stroke="var(--red)" stroke-width="5"/></svg>
      <div><h3>Your freedom starts with Fernlow!</h3><p>Our agents work around the clock to post your bail quickly and discreetly. We explain every step, handle the paperwork with the court and keep your family informed until you walk out the door and head home.</p></div>
    </div>
    <div class="about-item">
      <svg class="about-icon" viewBox="0 0 60 60"><rect x="10" y="8" width="26" height="44" fill="var(--blue)"/><path d="M30 30 H54 M46 22 L54 30 L46 38" stroke="var(--blue)" stroke-width="5" fill="none"/></svg>
      <div><h3>Fernlow gets you out. Fernlow gets you home</h3><p>We are licensed in every county we serve and know local jails well. Most releases are completed within hours, and flexible payment plans mean money never has to stand between you and the people you love most.</p></div>
    </div>
    <div class="about-item">
      <svg class="about-icon" viewBox="0 0 60 60"><rect x="8" y="12" width="44" height="40" rx="3" fill="none" stroke="var(--red)" stroke-width="4"/><rect x="8" y="12" width="44" height="10" fill="var(--red)"/><path d="M20 36 L27 43 L40 29" stroke="var(--red)" stroke-width="4" fill="none"/></svg>
      <div><h3>We guarantee your bail!</h3><p>One call starts the process. We confirm the charges, set the bond amount and meet you at the facility. Our team stays with your case through every court date so nothing is missed and your bond stays secure.</p></div>
    </div>
  </div>
</section>

<section class="offer">
  <h2 class="section-title">What We Offer</h2>
  <p class="section-sub">At Fernlow Bails, we deal with:</p>
  <div class="offer-grid">
    <div class="offer-item"><h4><svg width="24" height="16" viewBox="0 0 24 16"><circle cx="6" cy="8" r="5" fill="none" stroke="var(--red)" stroke-width="2.5"/><circle cx="18" cy="8" r="5" fill="none" stroke="var(--red)" stroke-width="2.5"/></svg>Felony Bails</h4><p>Fast release on felony charges of any size. Our agents review the case, post the bond and guide your family through each court appearance.</p></div>
    <div class="offer-item"><h4><svg width="24" height="16" viewBox="0 0 24 16"><rect x="2" y="2" width="12" height="7" fill="var(--dark)" transform="rotate(-30 8 6)"/><rect x="10" y="8" width="12" height="3" fill="var(--dark)" transform="rotate(-30 16 9)"/></svg>Drug Charges Bails</h4><p>Confidential help for drug related arrests. We work quickly with the court to secure release and explain every condition of the bond clearly.</p></div>
    <div class="offer-item"><h4><svg width="24" height="16" viewBox="0 0 24 16"><circle cx="6" cy="8" r="5" fill="none" stroke="var(--dark)" stroke-width="2.5"/><circle cx="18" cy="8" r="5" fill="none" stroke="var(--dark)" stroke-width="2.5"/></svg>Sex Crime Bails</h4><p>Discreet, respectful bond service for serious charges. Our staff handles paperwork privately and keeps your case moving without unwanted attention at all.</p></div>
    <div class="offer-item"><h4><svg width="24" height="16" viewBox="0 0 24 16"><rect x="3" y="3" width="18" height="10" rx="2" fill="var(--dark)"/></svg>DUI Bails</h4><p>Arrested for driving under the influence? We post DUI bonds day or night and help you understand next steps before your first hearing.</p></div>
    <div class="offer-item"><h4><svg width="24" height="16" viewBox="0 0 24 16"><rect x="3" y="4" width="18" height="9" fill="none" stroke="var(--dark)" stroke-width="2.5"/><path d="M3 4 L12 0 L21 4" stroke="var(--dark)" stroke-width="2" fill="none"/></svg>Theft Bails</h4><p>From petty theft to burglary, we arrange bonds for every level of charge and offer payment plans that fit your household budget.</p></div>
    <div class="offer-item"><h4><svg width="24" height="16" viewBox="0 0 24 16"><circle cx="12" cy="8" r="7" fill="none" stroke="var(--dark)" stroke-width="2.5"/><path d="M12 4 V8 L15 10" stroke="var(--dark)" stroke-width="2" fill="none"/></svg>24/7 Instant Public Service</h4><p>Jail does not keep office hours and neither do we. Call any time and a licensed agent will answer and start your release.</p></div>
  </div>
</section>

<section class="service" role="img" aria-label="Photo of a judge's gavel resting on an open law book">
  <div class="service-box"><h2>Our Service Area</h2><p>At Fernlow, our process is fast, professional and effective.</p></div>
</section>

<section class="newsletter">
  <h2>Newsletter Sign Up</h2>
  <div class="signup"><span>Enter your email address...</span><b><svg width="16" height="12" viewBox="0 0 16 12"><rect x="1" y="1" width="14" height="10" fill="none" stroke="var(--red)" stroke-width="2"/><path d="M1 1 L8 7 L15 1" stroke="var(--red)" stroke-width="2" fill="none"/></svg></b></div>
</section>

<footer class="footer"><span>Copyright © 2015 fernlowbails | Privacy Policy</span><div class="social"><span></span><span></span><span></span><span></span></div></footer>
</body>
</html>
```